Boutique custom software development company needs new business card

Our nearly 20 year old custom software development company would like to better include the fact that we are now providing Bitcoin services. These new services are B2B include education (how to acquire and securely hold Bitcoin) and integrating Bitcoin payments into existing ecommerce sites or other existing systems. Please keep the card clean and simple. Attached is our current design and some other files. vextorial.com

Target Market(s)

businesses owners interested in long term relationship

Industry/Entity Type

Custom software development and Bitcoin

Contact Information for Business Card

Dale Parker, dale@vextorial.com, vextorial.com, (888) 555-VXTRL

Font styles to use
Other font styles liked:
• monospace

Requirements
Must have
• double-sided
Nice to have
• clean and simple
Should not have
• physical address

```html
<!DOCTYPE html>
<html lang="en">
<head>
<meta charset="utf-8">
<title>Vextorial business card</title>
<link rel="stylesheet" href="https://fonts.googleapis.com/css2?family=Space+Mono:wght@400;700&family=Roboto+Mono:wght@400&family=Open+Sans:wght@400&display=swap">
<style>
  :root {
    --backdrop: #131416;
    --navy: #0b1738;
    --navy-deep: #091331;
    --blue: #4a7cc4;
    --orange: #f07f1f;
    --ink: #e9eef7;
  }
  * { box-sizing: border-box; margin: 0; padding: 0; }
  html, body { width: 1200px; height: 936px; overflow: hidden; }
  body {
    background: var(--backdrop);
    display: flex;
    flex-direction: column;
    align-items: center;
    justify-content: center;
    gap: 56px;
  }
  .card {
    position: relative;
    width: 560px;
    height: 320px;
    background: var(--navy);
    overflow: hidden;
    box-shadow: 0 10px 30px rgba(0,0,0,.5);
  }
  /* front */
  .brand-mark {
    position: absolute;
    top: 26px;
    right: 40px;
    display: flex;
    align-items: center;
    gap: 8px;
    font-family: "Space Mono", monospace;
    font-weight: 700;
    font-size: 18px;
    color: var(--blue);
  }
  .brand-mark .square { width: 16px; height: 16px; background: var(--blue); }
  .holder-name {
    position: absolute;
    left: 36px;
    top: 176px;
    font-family: "Space Mono", monospace;
    font-weight: 700;
    font-size: 27px;
    color: var(--blue);
    letter-spacing: .5px;
  }
  .divider {
    position: absolute;
    left: 30px;
    right: 20px;
    top: 222px;
    height: 1px;
    background: var(--blue);
    opacity: .7;
  }
  .contact-list {
    position: absolute;
    left: 40px;
    top: 234px;
    list-style: none;
    font-family: "Roboto Mono", monospace;
    font-size: 14px;
    line-height: 20px;
    color: var(--ink);
  }
  .contact-list li { display: flex; align-items: center; gap: 8px; }
  .contact-list svg { width: 12px; height: 12px; fill: var(--blue); }
  .website {
    position: absolute;
    right: 22px;
    bottom: 26px;
    font-family: "Roboto Mono", monospace;
    font-size: 13px;
    color: var(--ink);
  }
  .edge-band {
    position: absolute;
    left: 0; right: 0; bottom: 0;
    height: 11px;
    display: flex;
  }
  .edge-band .orange { flex: 0 0 77%; background: var(--orange); }
  .edge-band .blue { flex: 1; background: var(--blue); margin-top: -3px; }
  /* back */
  .card-back { background: var(--navy-deep); }
  .back-lockup {
    position: absolute;
    inset: 0;
    display: flex;
    flex-direction: column;
    align-items: center;
    justify-content: center;
    gap: 4px;
  }
  .back-name {
    font-family: "Space Mono", monospace;
    font-weight: 700;
    font-size: 38px;
    color: var(--blue);
    letter-spacing: 1px;
  }
  .tagline {
    font-family: "Open Sans", sans-serif;
    font-size: 14px;
    color: var(--blue);
  }
</style>
</head>
<body>
  <section class="card card-front">
    <div class="brand-mark"><span class="square"></span>VEXTORIAL</div>
    <h1 class="holder-name">Dale Parker</h1>
    <div class="divider"></div>
    <ul class="contact-list">
      <li><svg viewBox="0 0 24 24" aria-hidden="true"><path d="M6.6 10.8a15.1 15.1 0 0 0 6.6 6.6l2.2-2.2a1 1 0 0 1 1-.25 11.4 11.4 0 0 0 3.6.57 1 1 0 0 1 1 1V20a1 1 0 0 1-1 1A17 17 0 0 1 3 4a1 1 0 0 1 1-1h3.5a1 1 0 0 1 1 1c0 1.25.2 2.45.57 3.6a1 1 0 0 1-.25 1z"/></svg>(888) 555-VXTRL</li>
      <li><svg viewBox="0 0 24 24" aria-hidden="true"><path d="M2 5h20v14H2z M2 5l10 8 10-8" /></svg>dale@vextorial.com</li>
    </ul>
    <div class="website">vextorial.com</div>
    <div class="edge-band"><span class="orange"></span><span class="blue"></span></div>
  </section>

  <section class="card card-back">
    <div class="back-lockup">
      <div class="back-name">VEXTORIAL</div>
      <div class="tagline">developer of custom applications</div>
    </div>
  </section>
</body>
</html>
```